Northfield Builders Guild Business card

We are looking for a new business card design with photo included.
Our business is a nonprofit construction contractor membership organization. We offer business education, assist with business setup and licensing, provide safety training, and provide a member directory.
URL: www.builderslinkguild.org
Color code:
CMYK: 0 cyan, 42 magenta, 100 yellow, 0 black for Print.
Hexidecimal: #FF9900
RGB: R 255; G 153; B 0

```html
<!DOCTYPE html>
<html lang="en">
<head>
<meta charset="utf-8">
<title>Northfield Builders Guild – Business Card</title>
<link rel="stylesheet" href="https://fonts.googleapis.com/css2?family=Montserrat:wght@700;800&family=Arimo:wght@400&display=swap">
<style>
  :root {
    --orange: #ff9900;
    --card-black: #0b0b0b;
    --band-grey: #e2e1e2;
    --white: #ffffff;
    --stage: #2a2a2a;
  }
  * { box-sizing: border-box; margin: 0; padding: 0; }
  html, body { width: 1200px; height: 1015px; overflow: hidden; }
  body {
    background: var(--stage);
    display: flex;
    flex-direction: column;
    align-items: center;
    justify-content: center;
    gap: 40px;
    font-family: "Montserrat", sans-serif;
  }
  .card {
    position: relative;
    width: 800px;
    height: 457px;
    background: var(--card-black);
    overflow: hidden;
  }

  /* Front */
  .front-name {
    position: absolute;
    left: 0; right: 0; top: 92px;
    text-align: center;
    color: var(--white);
    font-weight: 800;
    text-transform: uppercase;
    line-height: 0.95;
  }
  .front-name .line-1 { font-size: 78px; letter-spacing: -1px; display: block; }
  .front-name .line-2 { font-size: 58px; letter-spacing: 6px; display: block; margin-top: 8px; }
  .services-band {
    position: absolute;
    left: 0; right: 0; bottom: 0;
    height: 150px;
    background: var(--orange);
    display: flex;
    flex-direction: column;
    justify-content: center;
    gap: 14px;
    padding: 0 60px;
  }
  .services-row { display: flex; gap: 34px; }
  .service {
    display: flex; align-items: center; gap: 9px;
    font-weight: 700; font-size: 17px; letter-spacing: 0.3px;
    text-transform: uppercase; color: var(--card-black);
  }
  .service::before {
    content: ""; width: 12px; height: 12px; border-radius: 50%;
    background: var(--card-black); flex: none;
  }

  /* Back */
  .brand-band {
    position: absolute; left: 0; right: 0; top: 0;
    height: 175px;
    background: var(--band-grey);
    display: flex; align-items: center; justify-content: center;
  }
  .brand-band .brand-name {
    font-weight: 800; font-size: 46px; letter-spacing: -0.5px;
    text-transform: uppercase; color: var(--card-black);
  }
  .person { position: absolute; left: 70px; top: 215px; }
  .person-name {
    color: var(--orange); font-weight: 800; font-size: 34px;
    text-transform: uppercase; letter-spacing: 0.5px;
  }
  .person-role {
    color: var(--white); font-weight: 700; font-size: 19px;
    text-transform: uppercase; letter-spacing: 1px; margin-top: 2px;
  }
  .contact-list {
    position: absolute; left: 70px; top: 318px;
    list-style: none;
    font-family: "Arimo", sans-serif; font-size: 20px; color: var(--white);
    display: flex; flex-direction: column; gap: 6px;
  }
  .contact-list li { display: flex; align-items: center; gap: 12px; }
  .contact-icon { width: 24px; height: 24px; flex: none; }
  .address {
    position: absolute; left: 470px; top: 238px;
    font-family: "Arimo", sans-serif; font-size: 21px; line-height: 1.3;
    color: var(--white); font-style: normal;
  }
  .website { color: var(--orange); margin-top: 12px; display: block; font-size: 19px; }
</style>
</head>
<body>

<section class="card card-front" aria-label="Business card front">
  <h1 class="front-name">
    <span class="line-1">Northfield</span>
    <span class="line-2">Builders Guild</span>
  </h1>
  <div class="services-band">
    <div class="services-row">
      <span class="service">Business education</span>
      <span class="service">Assist with business setup and licensing</span>
    </div>
    <div class="services-row">
      <span class="service">Provide safety training</span>
      <span class="service">Provide a member directory</span>
    </div>
  </div>
</section>

<section class="card card-back" aria-label="Business card back">
  <div class="brand-band">
    <span class="brand-name">Northfield Builders Guild</span>
  </div>

  <div class="person">
    <h2 class="person-name">Daniel Reyes</h2>
    <p class="person-role">Managing Director</p>
  </div>

  <ul class="contact-list">
    <li>
      <svg class="contact-icon" viewBox="0 0 24 24" aria-hidden="true"><circle cx="12" cy="12" r="12" fill="#ff9900"/><path d="M8 6.5l2 2.2-1.2 1.6c.8 1.7 2 2.9 3.7 3.7l1.6-1.2 2.2 2-1.2 1.7c-3.8-.6-7-3.8-7.6-7.6z" fill="#fff"/></svg>
      (555) 210-4471
    </li>
    <li>
      <svg class="contact-icon" viewBox="0 0 24 24" aria-hidden="true"><circle cx="12" cy="12" r="12" fill="#ff9900"/><rect x="8.5" y="5.5" width="7" height="13" rx="1.2" fill="none" stroke="#fff" stroke-width="1.6"/><circle cx="12" cy="16.2" r=".9" fill="#fff"/></svg>
      800-555-0143
    </li>
    <li>
      <svg class="contact-icon" viewBox="0 0 24 24" aria-hidden="true"><circle cx="12" cy="12" r="12" fill="#ff9900"/><rect x="8.5" y="5.5" width="7" height="4" fill="#fff"/><rect x="6" y="10" width="12" height="6" rx="1" fill="#fff"/><rect x="8.5" y="14" width="7" height="4.5" fill="#fff" stroke="#ff9900" stroke-width=".8"/></svg>
      555.619.0290
    </li>
    <li>
      <svg class="contact-icon" viewBox="0 0 24 24" aria-hidden="true"><circle cx="12" cy="12" r="12" fill="#ff9900"/><rect x="6" y="8" width="12" height="8.5" fill="#fff"/><path d="M6 8l6 5 6-5" fill="none" stroke="#ff9900" stroke-width="1.2"/></svg>
      hello@nbguild.org
    </li>
  </ul>

  <address class="address">
    2450 Ridgeway Ave<br>
    Suite #200, Fairview<br>
    OR 97000
    <span class="website">www.builderslinkguild.org</span>
  </address>
</section>

</body>
</html>
```